Visitenkarten/Briefpaier/Kassenkassenbelege für Juwelier
Zielgruppe
Mittelständischer Juwelier mit zwei Filialen. Klassischer Schmuck, Uhren und Modeschmuck
Aufgabenstellung
Es müssen für zwei Geschäfte Visitenkarten, Briefpapier (A4) und Kassenkassenbelege (A6) erstellt werden. Logo und Typo im Anhang. Ein Farbkonzept besteht noch nicht. Die Idee geht in Richtung Bordeaux-Rot.
Generell:
(1) Sieht erstmal nach viel Beschreibung aus, bitte nicht entmutigen lassen, sind zu 90% nur austauschbare Inhalts-/Kontaktdaten.
(2) Für meine Zwecke reicht es vollkommen aus, wenn bei den Vorschlägen zur Arbeitsersparnis erstmal nur mit einer Adresse gearbeitet wird. Wenn ich dann den zutreffenden Designvorschlag gefunden habe, können wir die zweite Adresse in dem ersten Format umsetzen. Ich denke das spart Zeit und Nerven.
(3) Bitte Angaben wie "Tel.:" oder "USt.- ID:" nicht wörtlich nehmen, es soll dabei klar sein worum es geht; wenn "Telefon" ausgeschrieben besser aussieht, bitte in der optisch ansprechenderen Form verwenden.
(4) Bei Fragen, bitte fragen!
(5) Viel Spass bei dem Projekt - Ich freu' mich auf die Vorschläge!
Visitenkarten(1):
Juwelier Brenneck GmbH
www.juwelier-brenneck-beispiel.de
Visitenkarten(2):
Visitenkarten(generell):
(1) Die einzelnen Daten können durch Hervorhebungen wie Adresse, Kontakt, Online/Internet unterteilt bzw. hervorgehoben werden.
(2) Die Visitenkarten sollen farbig gedruckt werden; geplant ist weiß als Hintergrund ist aber nicht zwingend bei einer guten anderen Idee
Briefpapier:
(1)Absender im Adressfeld für DIN-lang Briefumschläge mit Fenster:
(2)Informationen im Footer/Seitenbereich:
Juwelier Brenneck Gmb..

```html
<!DOCTYPE html>
<html lang="de">
<head>
<meta charset="utf-8">
<title>Juwelier Brenneck – Briefpapier und Umschlag</title>
<link href="https://fonts.googleapis.com/css2?family=Source+Sans+3:wght@400;600;700&display=swap" rel="stylesheet">
<style>
  :root {
    --bg: #f6f6f6;
    --paper: #ffffff;
    --teal: #023646;
    --stone: #7a7068;
    --mark: #9a9a9a;
    --window: #e2e2e2;
  }
  * { margin: 0; padding: 0; box-sizing: border-box; }
  html, body { width: 1200px; height: 1000px; overflow: hidden; background: var(--bg); }
  body { position: relative; font-family: "Source Sans 3", "Source Sans Pro", sans-serif; }

  .crop-mark { position: absolute; background: var(--mark); }
  .crop-mark.v { width: 1px; height: 25px; }
  .crop-mark.h { height: 1px; width: 25px; }

  .sheet { position: absolute; background: var(--paper); box-shadow: 1px 2px 4px rgba(0,0,0,.25); }

  /* Letterhead */
  .letterhead { left: 42px; top: 50px; width: 533px; height: 753px; }
  .brand { position: absolute; display: flex; flex-direction: column; align-items: center; }
  .brand-square { width: 30px; height: 30px; background: var(--teal); }
  .brand-name { margin-top: 10px; font-size: 17px; font-weight: 700; letter-spacing: 1.5px; color: var(--stone); white-space: nowrap; }
  .letterhead .brand { left: 23px; width: 170px; top: 22px; }
  .divider-v { position: absolute; left: 402px; top: 0; width: 1px; height: 135px; background: var(--teal); }
  .contact { position: absolute; right: 25px; top: 34px; text-align: right; color: var(--stone); font-size: 7.5px; line-height: 10.8px; }
  .contact .company { font-size: 9.5px; font-weight: 600; line-height: 13px; }
  .contact .gap { height: 10px; }
  .fold-mark { position: absolute; left: 0; width: 18px; height: 1px; background: #ccc; }
  .footer-rule { position: absolute; left: 0; right: 0; top: 706px; height: 2px; background: var(--teal); }
  .footer-col { position: absolute; color: var(--teal); font-size: 6.6px; line-height: 8px; }
  .footer-sep { position: absolute; top: 712px; width: 1px; height: 29px; background: #ccc; }

  /* Envelope front */
  .envelope-front { left: 623px; top: 100px; width: 559px; height: 286px; }
  .sender { position: absolute; left: 34px; top: 26px; font-size: 7.2px; line-height: 10.8px; color: var(--stone); }
  .sender .company { font-size: 9.5px; font-weight: 700; color: var(--teal); line-height: 12px; }
  .address-window { position: absolute; left: 38px; top: 153px; width: 223px; height: 89px; border-radius: 12px; border: 1px solid var(--window); box-shadow: inset 1px 2px 3px rgba(0,0,0,.18); }
  .envelope-front .brand { right: 20px; width: 170px; top: 142px; }
  .envelope-band { position: absolute; left: 0; right: 0; bottom: 0; height: 6px; background: var(--teal); }

  /* Envelope back */
  .envelope-back { left: 623px; top: 475px; width: 559px; height: 285px; }
  .flap { position: absolute; left: 0; top: 0; }
  .flap-square { position: absolute; left: 266px; top: 0; width: 28px; height: 28px; background: var(--teal); }
</style>
</head>
<body>
  <!-- crop marks around letterhead -->
  <div class="crop-mark v" style="left:42px;top:12px"></div>
  <div class="crop-mark v" style="left:575px;top:12px"></div>
  <div class="crop-mark v" style="left:42px;top:816px"></div>
  <div class="crop-mark v" style="left:575px;top:816px"></div>
  <div class="crop-mark h" style="left:4px;top:50px"></div>
  <div class="crop-mark h" style="left:588px;top:50px"></div>
  <div class="crop-mark h" style="left:4px;top:803px"></div>
  <div class="crop-mark h" style="left:588px;top:803px"></div>

  <section class="sheet letterhead" aria-label="Briefpapier A4">
    <div class="brand">
      <div class="brand-square"></div>
      <div class="brand-name">Juwelier Brenneck</div>
    </div>
    <div class="divider-v"></div>
    <address class="contact" style="font-style:normal">
      <div class="company">Juwelier Brenneck GmbH</div>
      <div>Lindenallee 12</div>
      <div>45127 Beispielstadt</div>
      <div class="gap"></div>
      <div>Tel.: 0201-123456</div>
      <div>Fax: 0201-123457</div>
      <div>info@juwelier-brenneck-beispiel.de</div>
      <div>www.juwelier-brenneck-beispiel.de</div>
    </address>
    <div class="fold-mark" style="top:268px"></div>
    <div class="fold-mark" style="top:520px"></div>
    <div class="footer-rule"></div>
    <div class="footer-col" style="left:65px;top:712px">Bankverbindung:<br>Musterbank AG Beispielstadt<br>IBAN: DE00 1234 5678 0000 1111 22<br>BIC: MUST DE 1X</div>
    <div class="footer-sep" style="left:207px"></div>
    <div class="footer-col" style="left:246px;top:716px">Steuernummer:<br>100/2000/3000<br>USt.- ID: DE 123456789</div>
    <div class="footer-sep" style="left:348px"></div>
    <div class="footer-col" style="left:411px;top:716px;font-size:7.4px;line-height:8.2px">Filiale:<br>Marktstraße 8<br>45999 Musterstadt</div>
  </section>

  <section class="sheet envelope-front" aria-label="Briefumschlag DIN lang, Vorderseite">
    <address class="sender" style="font-style:normal">
      <div class="company">Juwelier Brenneck GmbH</div>
      <div>Lindenallee 12</div>
      <div>45127 Beispielstadt</div>
    </address>
    <div class="address-window"></div>
    <div class="brand">
      <div class="brand-square"></div>
      <div class="brand-name">Juwelier Brenneck</div>
    </div>
    <div class="envelope-band"></div>
  </section>

  <section class="sheet envelope-back" aria-label="Briefumschlag DIN lang, Rückseite">
    <svg class="flap" width="559" height="70" viewBox="0 0 559 70">
      <path d="M0 1 L30 54 Q36 63 50 63 L500 63 Q512 63 520 55 L559 3" fill="none" stroke="#e0e0e0" stroke-width="1.5"/>
    </svg>
    <div class="flap-square"></div>
  </section>
</body>
</html>
```